Business Card Design Project

I need a business card designed from scratch. I have an existing logo that I can upload in Illustrator for modification or redesign.

The Company is called Query Lanterns http://querylanterns.com.au and we provide Search Engine Optimization services to Australian businesses. The current logo signifies an increase in visitors, profits etc...

There are no restrictions as to the redesign - colours, style etc are all open to change.

Cards will be full colour and one sided printed at http://www.cardmoxel.com.au so check their requirements for file format and sizes etc.

I will expect all original files upon completion of project.

Target Market(s)

Any business with a web site looking to improve their search engine rankings

Industry/Entity Type

Business

Requirements
Must have
• I like modern, sleek designs. Clean, not fussy, uncluttered.

```html
<!DOCTYPE html>
<html lang="en">
<head>
<meta charset="utf-8">
<title>Query Lanterns — Business Card</title>
<link rel="stylesheet" href="https://fonts.googleapis.com/css2?family=Open+Sans:wght@400;600;700;800&display=swap">
<style>
  :root {
    --backdrop: #ece9e4;
    --card: #ffffff;
    --brand-blue: #1a74b9;
    --brand-yellow: #f6c500;
    --ink: #3a3a3a;
    --rule-dark: #3b4050;
    --white: #ffffff;
  }
  * { box-sizing: border-box; margin: 0; padding: 0; }
  html, body {
    width: 1200px; height: 460px; overflow: hidden;
    background: var(--backdrop);
    font-family: "Open Sans", Arial, sans-serif;
  }
  .stage { position: relative; width: 1200px; height: 460px; }
  .card {
    position: absolute; top: 77px;
    width: 543px; height: 308px;
    background: var(--card);
    border-radius: 14px;
    overflow: hidden;
    box-shadow: 0 3px 8px rgba(0,0,0,0.25);
  }
  .card--front { left: 44px; }
  .card--back { left: 614px; }

  .brand {
    position: absolute; display: flex; align-items: center; gap: 12px;
    font-weight: 800; color: var(--brand-blue);
  }
  .brand__dot {
    width: 22px; height: 22px; border-radius: 50%;
    background: var(--brand-yellow);
  }
  .card--front .brand { left: 0; right: 0; top: 92px; justify-content: center; font-size: 40px; letter-spacing: -0.5px; }
  .card--back .brand { left: 0; right: 0; top: 118px; justify-content: center; font-size: 40px; letter-spacing: -0.5px; }

  .contact {
    position: absolute; left: 22px; top: 221px;
    display: grid; grid-template-columns: auto auto auto; column-gap: 12px; row-gap: 2px;
    font-size: 13.5px; color: var(--ink); line-height: 18px;
  }
  .contact__item { display: flex; align-items: center; gap: 4px; white-space: nowrap; }
  .contact__icon { width: 10px; height: 10px; flex: none; }

  .front-rule {
    position: absolute; left: 0; right: 0; top: 262px; height: 3px;
    background: var(--brand-yellow);
  }
  .front-band {
    position: absolute; left: 0; right: 0; top: 267px; bottom: 0;
    background: var(--brand-blue);
    display: flex; align-items: center; justify-content: center; gap: 8px;
    color: var(--white); padding-bottom: 4px;
  }
  .front-band__name { font-weight: 700; font-size: 16px; }
  .front-band__title { font-size: 13.5px; }

  .back-rule {
    position: absolute; left: 0; right: 0; top: 266px; height: 2px;
    background: var(--rule-dark);
  }
  .back-band {
    position: absolute; left: 0; right: 0; top: 271px; bottom: 0;
    background: var(--brand-blue);
    display: flex; align-items: center; justify-content: center;
    color: var(--white); font-size: 13px; letter-spacing: 3px; padding-bottom: 3px;
  }
</style>
</head>
<body>
<main class="stage">
  <section class="card card--front" aria-label="Card front">
    <div class="brand"><span class="brand__dot"></span><span class="brand__name">Query Lanterns</span></div>

    <div class="contact">
      <span>00Floor Street, City Name</span>
      <span class="contact__item">
        <svg class="contact__icon" viewBox="0 0 10 10"><path d="M2 1 L4 1 L4.5 3 L3.3 4 Q4.5 6 6 6.7 L7 5.5 L9 6 L9 8 Q5 9 1.5 4.5 Q1 2.5 2 1Z" fill="var(--brand-blue)"/></svg>
        098 765 4321
      </span>
      <span class="contact__item">
        <svg class="contact__icon" viewBox="0 0 10 10"><rect x="0.5" y="2" width="9" height="6.5" fill="var(--brand-blue)"/><path d="M0.5 2 L5 5.5 L9.5 2" stroke="#fff" stroke-width="0.9" fill="none"/></svg>
        enquiry@querylanterns.com.au
      </span>
      <span>State Name, Contry Name</span>
      <span class="contact__item">
        <svg class="contact__icon" viewBox="0 0 10 10"><rect x="2.5" y="0.5" width="5" height="9" rx="1" fill="var(--brand-blue)"/><rect x="3.4" y="1.6" width="3.2" height="5" fill="#fff"/></svg>
        098 765 4321
      </span>
      <span class="contact__item">
        <svg class="contact__icon" viewBox="0 0 10 10"><circle cx="5" cy="5" r="4.5" fill="var(--brand-blue)"/><path d="M0.5 5 H9.5 M5 0.5 Q2.5 5 5 9.5 M5 0.5 Q7.5 5 5 9.5" stroke="#fff" stroke-width="0.7" fill="none"/></svg>
        www.querylanterns.com.au
      </span>
    </div>

    <div class="front-rule"></div>
    <div class="front-band">
      <span class="front-band__name">Your Name</span>
      <span class="front-band__title">Title</span>
    </div>
  </section>

  <section class="card card--back" aria-label="Card back">
    <div class="brand"><span class="brand__dot"></span><span class="brand__name">Query Lanterns</span></div>
    <div class="back-rule"></div>
    <div class="back-band">www.querylanterns.com.au</div>
  </section>
</main>
</body>
</html>
```